Freelance Translator in Need of a Business Card

I am a freelance Japanese to English translator. I work in the video game localization industry and do literary translation in my spare time. I would like to have both the English word 'Translator' and the Japanese '翻訳者' in the job title. The final design should evoke trust, openness, and reliability.

Target Market(s)

Video game localization companies
Japanese comic book artists

Industry/Entity Type

Business

Contact Information for Business Card

Daniel Forsvik, Translator
dan.forsvik@quellmail.net
torvenwords.com
natter: @torven_wd

Colors

Designer to choose colors to be used in the design.

```html
<!DOCTYPE html>
<html lang="en">
<head>
<meta charset="utf-8">
<title>Torven Words – Business Card</title>
<link rel="stylesheet" href="https://fonts.googleapis.com/css2?family=Playfair+Display:wght@400;700&family=Noto+Serif+JP:wght@400;600&display=swap">
<style>
  :root {
    --ink: #141414;
    --paper: #ffffff;
    --band-light: #ececec;
    --muted: #555555;
    --stage: #e4e2de;
  }
  * { margin: 0; padding: 0; box-sizing: border-box; }
  html, body {
    width: 1200px;
    height: 892px;
    overflow: hidden;
    background: var(--stage);
  }
  .canvas {
    position: relative;
    width: 1200px;
    height: 892px;
    display: flex;
    align-items: center;
    justify-content: center;
    gap: 40px;
  }
  .card {
    position: relative;
    width: 540px;
    height: 309px;
    overflow: hidden;
    box-shadow: 0 6px 18px rgba(0,0,0,0.18);
  }

  /* Front side */
  .card-front { background: var(--paper); color: var(--ink); }
  .brand-name {
    position: absolute;
    left: 42px;
    top: 60px;
    font-family: "Playfair Display", serif;
    font-weight: 700;
    font-size: 42px;
    line-height: 1.2;
    letter-spacing: 0.5px;
  }
  .identity {
    position: absolute;
    right: 236px;
    top: 140px;
    font-family: "Playfair Display", "Noto Serif JP", serif;
    color: var(--muted);
    text-align: right;
  }
  .identity .person { font-size: 17px; line-height: 1.2; }
  .identity .role { font-size: 14px; line-height: 1.4; }
  .identity .role .ja { font-family: "Noto Serif JP", serif; color: var(--ink); }
  .divider {
    position: absolute;
    left: 318px;
    top: 128px;
    width: 2px;
    height: 94px;
    background: var(--ink);
  }
  .contact {
    position: absolute;
    left: 334px;
    top: 150px;
    list-style: none;
    font-family: "Playfair Display", serif;
    font-size: 12.5px;
    color: var(--ink);
  }
  .contact li { display: flex; align-items: center; gap: 7px; line-height: 22px; white-space: nowrap; }
  .contact svg { width: 12px; height: 12px; flex: none; }
  .social-band {
    position: absolute;
    left: 0; right: 0; bottom: 0;
    height: 64px;
    background: var(--ink);
    display: flex;
    align-items: center;
    justify-content: center;
    font-family: "Playfair Display", serif;
    font-size: 15px;
    color: var(--paper);
    letter-spacing: 0.3px;
  }

  /* Back side */
  .card-back {
    background: var(--ink);
    display: flex;
    align-items: center;
  }
  .back-band {
    width: 100%;
    height: 148px;
    background: var(--band-light);
    display: flex;
    align-items: center;
    justify-content: center;
  }
  .back-band .brand-caps {
    font-family: "Playfair Display", serif;
    font-weight: 700;
    font-size: 40px;
    text-transform: uppercase;
    letter-spacing: 1px;
    color: var(--ink);
  }
</style>
</head>
<body>
<main class="canvas">
  <section class="card card-front" aria-label="Business card front">
    <h1 class="brand-name">Torven Words</h1>
    <div class="identity">
      <p class="person">Daniel Forsvik</p>
      <p class="role">Translator <span class="ja">翻訳者</span></p>
    </div>
    <div class="divider"></div>
    <ul class="contact">
      <li>
        <svg viewBox="0 0 12 12" aria-hidden="true"><rect x="0.5" y="2" width="11" height="8" fill="#141414"/><path d="M0.5 2 L6 7 L11.5 2" fill="none" stroke="#fff" stroke-width="1"/></svg>
        dan.forsvik@quellmail.net
      </li>
      <li>
        <svg viewBox="0 0 12 12" aria-hidden="true"><circle cx="6" cy="6" r="5.5" fill="#141414"/><ellipse cx="6" cy="6" rx="2.2" ry="5.5" fill="none" stroke="#fff" stroke-width="0.8"/><line x1="0.5" y1="6" x2="11.5" y2="6" stroke="#fff" stroke-width="0.8"/></svg>
        www.torvenwords.com
      </li>
    </ul>
    <div class="social-band">natter: @torven_wd</div>
  </section>

  <section class="card card-back" aria-label="Business card back">
    <div class="back-band">
      <span class="brand-caps">Torven Words</span>
    </div>
  </section>
</main>
</body>
</html>
```